Rack Card for Charter Sail Boat business in SF Bay

We are in need of a rack card design to highlight the business to tourists and locals. 2 sided card 3.86" x 8.39" (full bleed)

We are looking for visually appleaing designs on the front and back but a little more detail on the back.

Use the info provided (text and info) on the website to include the 3 key services (Quick, 1/2 day, fullday) and aspects of the boat, location and other key info for customers (not prices). DO NOT INCLUDE ALL THIS TEXT please pick the elements you would like to fit your design and inform the customer as you would like about the business.

I can also provide photos directly from the video if you think those would fit your design. If video doesn't work on this upload you can view it at the website or facebook page (www.fb.com/tidewrenmarinellc)

Target Market(s)

Tourists and locals to san francisco east bay. 25 - 55 years old. Men and women.

Industry/Entity Type

Entertainment

Colors
0455a3
ec1f27
f3f1f8

Requirements
Must have
• Highlight services, key contact information (email, phone, website site), Visual impact
• 2-sided card - 3.86" x 8.39" (98 x 213 mm)
Nice to have
• facebook link, electric engine(green),

```html
<!DOCTYPE html>
<html lang="en">
<head>
<meta charset="utf-8">
<title>Tidewren Marine – Rack Card</title>
<link href="https://fonts.googleapis.com/css2?family=Libre+Baskerville:ital@0;1&family=Arimo&family=Roboto+Condensed:wght@300;700&display=swap" rel="stylesheet">
<style>
:root{
  --navy:#0455a3;
  --deep:#0b2e7a;
  --red:#ec1f27;
  --paper:#f3f1f8;
  --white:#ffffff;
  --yellow:#f5e21a;
  --charcoal:#3d3d3d;
  --map:#cfe3f3;
  --ink:#111111;
  --stage:#e6e4ea;
}
*{margin:0;padding:0;box-sizing:border-box}
html,body{width:1200px;height:1200px;overflow:hidden;background:var(--stage)}
.canvas{position:relative;width:1200px;height:1200px}
.card{position:absolute;top:123px;width:445px;height:967px;overflow:hidden;background:var(--white);box-shadow:0 4px 14px rgba(0,0,0,.25)}
.card--front{left:117px}
.card--back{left:642px;background:var(--deep)}
.card svg.shapes{position:absolute;inset:0}
.abs{position:absolute}
.serif{font-family:"Libre Baskerville",Georgia,serif}
.body{font-family:Arimo,Arial,sans-serif;font-size:11.8px;line-height:14px;color:var(--ink)}

/* front */
.hero-photo{left:0;top:0;width:445px;height:290px;background:linear-gradient(180deg,#8fb3cf 0%,#f3c77a 45%,#f0a94a 55%,#3c5f7a 70%,#1f3c57 100%)}
.brand{left:225px;top:40px;width:215px;display:flex;align-items:center;gap:8px}
.brand__dot{width:16px;height:16px;border-radius:50%;background:var(--navy);flex:none}
.brand__name{font-family:"Libre Baskerville",Georgia,serif;font-size:22px;color:var(--navy);line-height:1.1}
.tagline{left:16px;top:285px;width:215px;font-family:"Libre Baskerville",Georgia,serif;font-style:italic;font-size:19.5px;line-height:32.5px;color:var(--white)}
.tagline em{color:var(--yellow);font-style:italic}
.photo-circle{position:absolute;border-radius:50%;border:6px solid var(--white);box-shadow:0 2px 6px rgba(0,0,0,.25)}
.feature h2{font-weight:400;font-size:28px;line-height:1;margin-bottom:9px}
.feature--red h2{color:var(--red)}
.feature--blue h2{color:var(--navy)}
.front-contact{left:20px;font-family:"Roboto Condensed","Arial Narrow",sans-serif;font-weight:700;font-size:16.5px;color:var(--white);display:flex;align-items:center;gap:8px;white-space:nowrap}
.front-contact svg{flex:none}

/* back */
.sea-top{left:0;top:0;width:445px;height:240px;background:linear-gradient(180deg,#1c3f8a 0%,#1a4aa0 55%,#123a8a 100%)}
.trip-title{left:18px;top:29px;font-size:30px;color:var(--white);font-weight:400}
.trip-copy{left:18px;top:75px;width:415px;color:var(--white);font-size:12px;line-height:14px}
.service{position:absolute;border-radius:50%;border:6px solid var(--white);display:flex;flex-direction:column;align-items:center;justify-content:center;text-align:center;padding:0 16px;box-shadow:0 3px 8px rgba(0,0,0,.3)}
.service h3{font-family:"Libre Baskerville",Georgia,serif;font-weight:400;color:var(--yellow);font-size:21px;line-height:24px;margin-bottom:8px}
.service p{font-family:"Roboto Condensed","Arial Narrow",sans-serif;font-weight:300;color:var(--white);font-size:13px;line-height:17px}
.service--quick{left:226px;top:202px;width:200px;height:200px;background:var(--red)}
.service--quick h3{white-space:nowrap}
.service--half{left:17px;top:386px;width:192px;height:192px;background:var(--deep)}
.service--half h3{white-space:nowrap}
.service--full{left:236px;top:583px;width:192px;height:192px;background:var(--charcoal)}
.sea-bottom{left:0;top:780px;width:445px;height:187px;background:linear-gradient(180deg,#1d4aa6 0%,#163f93 45%,#0f2f78 100%)}
.badge{left:13px;top:805px;width:76px;height:76px;border-radius:50%;background:var(--navy);border:4px solid var(--white)}
.contact-title{left:170px;top:845px;font-size:28px;color:var(--white);font-weight:400}
.back-contact{position:absolute;left:0;width:445px;display:flex;justify-content:center;gap:14px;font-family:"Roboto Condensed","Arial Narrow",sans-serif;font-weight:700;color:var(--white);white-space:nowrap}
.back-contact span{display:flex;align-items:center;gap:5px}
.back-contact svg{flex:none}
.social-dot{width:15px;height:15px;border-radius:50%;border:1.6px solid var(--white);display:inline-block;flex:none}
</style>
</head>
<body>
<div class="canvas">

  <!-- FRONT -->
  <section class="card card--front">
    <div class="abs hero-photo" role="img" aria-label="Sunset over San Francisco Bay seen from the deck of a sailboat"></div>
    <svg class="shapes" width="445" height="967" viewBox="0 0 445 967" aria-hidden="true">
      <path d="M0,250 Q150,190 310,270 L445,335 L445,360 L300,285 Q150,205 0,265Z" fill="var(--red)"/>
      <path d="M0,265 Q150,205 300,285 L445,360 L445,430 L230,465 Q80,480 0,525Z" fill="var(--navy)"/>
      <path d="M50,508 Q150,468 260,458 L445,448 L445,458 L262,466 Q150,476 50,515Z" fill="var(--red)"/>
      <path d="M300,690 Q380,680 445,525 L445,660 Q390,670 300,690Z" fill="var(--red)"/>
      <path d="M0,870 Q120,845 240,895 Q340,935 445,875 L445,967 L0,967Z" fill="var(--navy)"/>
      <path d="M280,905 Q370,925 445,840 L445,875 Q340,935 280,905Z" fill="var(--red)"/>
    </svg>
    <div class="abs brand"><span class="brand__dot"></span><span class="brand__name">Tidewren Marine</span></div>
    <p class="abs tagline">Enjoy an amazing experience aboard <em>Tidewren</em> and view San Francisco and the rest of the bay</p>

    <div class="photo-circle" style="left:231px;top:161px;width:216px;height:216px;background:linear-gradient(160deg,#f2f2f2 0%,#c9d6e0 40%,#3f6fa3 70%,#1d3f6b 100%)" role="img" aria-label="Sail and rigging over the bay"></div>
    <div class="photo-circle" style="left:299px;top:317px;width:192px;height:192px;background:linear-gradient(160deg,#c9a27a,#8a6a55 60%,#5b5b7a)" role="img" aria-label="Cabin interior below deck"></div>
    <div class="photo-circle" style="left:223px;top:361px;width:136px;height:136px;background:linear-gradient(180deg,#7fa7d6 0%,#3b5f8a 45%,#4a7ec4 60%,#1e4d92 100%)" role="img" aria-label="Sunlight glittering on the bay water"></div>
    <div class="photo-circle" style="left:187px;top:453px;width:200px;height:200px;background:linear-gradient(180deg,#9fc0e0 0%,#d9dfe3 35%,#2a5a7a 55%,#3e7a5e 100%)" role="img" aria-label="The yacht moored at the marina"></div>

    <div class="abs feature feature--red" style="left:20px;top:538px;width:165px">
      <h2 class="serif">Modern</h2>
      <p class="body">Tidewren is completely electric which means no diesel smells, noise or vibration to suffer. New electrics, plumbing, toilets, and deck areas compliment the elegant lines.</p>
    </div>
    <div class="abs feature feature--blue" style="left:21px;top:709px;width:185px">
      <h2 class="serif">Entertaining</h2>
      <p class="body">Experience the thrill of sailing Tidewren while we explore Alcatraz and Angel Islands', The Golden Gate and Bay Bridges, the City front or the many other hidden gems.</p>
    </div>
    <div class="abs feature feature--red" style="left:249px;top:687px;width:180px">
      <h2 class="serif">Safe</h2>
      <p class="body">We carry aboard everything to make your time aboard safe. Life preservers and USCG bulky ones as well as modern self inflating slim comfortable life jackets. Also loaded for every trip is a complete first aid kit, AED, EPIRB, and many other safety items</p>
    </div>

    <div class="abs front-contact" style="top:902px">
      <svg width="19" height="19" viewBox="0 0 20 20"><circle cx="10" cy="10" r="8.8" fill="none" stroke="#fff" stroke-width="1.6"/><path d="M7 5.5l1.6 2.4-1 1.2c.6 1.3 1.5 2.2 2.8 2.8l1.2-1 2.4 1.6-.8 1.6c-3.6-.2-6.8-3.4-7-7z" fill="#fff"/></svg>
      +1 (555) 014 SAIL (7245)
    </div>
    <div class="abs front-contact" style="top:930px">
      <svg width="19" height="14" viewBox="0 0 20 14"><rect x="1" y="1" width="18" height="12" fill="none" stroke="#fff" stroke-width="1.6"/><path d="M1 1l9 7 9-7M1 13l6.5-6M19 13l-6.5-6" fill="none" stroke="#fff" stroke-width="1.4"/></svg>
      Bookings@TidewrenMarine.com
    </div>
  </section>

  <!-- BACK -->
  <section class="card card--back">
    <div class="abs sea-top" role="img" aria-label="Open water of the bay with hills on the horizon"></div>
    <svg class="shapes" width="445" height="967" viewBox="0 0 445 967" aria-hidden="true">
      <path d="M0,195 Q120,150 230,190 Q340,230 445,190 L445,800 Q300,760 200,800 Q100,830 0,790Z" fill="var(--map)" role="img" aria-label="Map of San Francisco Bay with the three cruise routes"/>
      <path d="M0,182 Q120,135 230,175 Q340,215 445,172 L445,192 Q340,232 230,192 Q120,152 0,197Z" fill="var(--red)"/>
      <path d="M0,420 Q120,370 230,400 Q340,430 445,370" fill="none" stroke="var(--navy)" stroke-width="3"/>
      <path d="M0,575 Q120,540 230,570 Q340,600 445,565" fill="none" stroke="var(--red)" stroke-width="3"/>
      <path d="M0,600 Q120,560 230,590 Q340,625 445,580" fill="none" stroke="var(--navy)" stroke-width="3"/>
    </svg>
    <div class="abs sea-bottom" role="img" aria-label="Bay water at dusk beneath the city skyline"></div>
    <svg class="shapes" width="445" height="967" viewBox="0 0 445 967" aria-hidden="true">
      <path d="M0,780 Q100,820 200,790 Q300,755 445,790 L445,760 Q300,725 200,770 Q100,810 0,770Z" fill="var(--red)"/>
    </svg>

    <h1 class="abs serif trip-title">The trip</h1>
    <p class="abs body trip-copy">When chartering Tidewren, the vessel is yours to direct anywhere within the time you wish to enjoy her. We do have a few old favorites that are always fun that we have listed below. These are just to provide an idea of the possible cruise as every trip takes into account your ideas and natures (tides, weather and currents) will.Our custom trips are simple to arrange and book, we simply ask for a minimum of 3 hours duration.</p>

    <div class="service service--quick">
      <h3>2 hour Blast</h3>
      <p>Could be a sunset sail, an early morning wake up cruise or a blast out into the bay anytime to find peace, fresh air and amazing views.</p>
    </div>
    <div class="service service--half">
      <h3>½ day Fun</h3>
      <p>A full morning, afternoon or evening out in the Bay seeing many of the main features and landmarks close to the Bay from the water. Actual duration 4-5 hours</p>
    </div>
    <div class="service service--full">
      <h3>Full Day Adventure</h3>
      <p>The day includes a complete circuit of the Bay and lunch at anchor. Actual duration 7-8 hours</p>
    </div>

    <div class="abs badge" role="img" aria-label="Licensed captain certification badge"></div>
    <h2 class="abs serif contact-title">Contact</h2>
    <div class="back-contact" style="top:903px;font-size:14.5px">
      <span><svg width="18" height="18" viewBox="0 0 20 20"><circle cx="10" cy="10" r="8.8" fill="none" stroke="#fff" stroke-width="1.6"/><path d="M7 5.5l1.6 2.4-1 1.2c.6 1.3 1.5 2.2 2.8 2.8l1.2-1 2.4 1.6-.8 1.6c-3.6-.2-6.8-3.4-7-7z" fill="#fff"/></svg>+1 (555) 014 SAIL (7245)</span>
      <span><svg width="19" height="13" viewBox="0 0 20 14"><rect x="1" y="1" width="18" height="12" fill="none" stroke="#fff" stroke-width="1.6"/><path d="M1 1l9 7 9-7M1 13l6.5-6M19 13l-6.5-6" fill="none" stroke="#fff" stroke-width="1.4"/></svg>Bookings@TidewrenMarine.com</span>
    </div>
    <div class="back-contact" style="top:935px;font-size:13.5px">
      <span><svg width="15" height="15" viewBox="0 0 20 20" fill="none" stroke="#fff" stroke-width="1.5"><circle cx="10" cy="10" r="8.5"/><ellipse cx="10" cy="10" rx="4" ry="8.5"/><path d="M1.5 10h17M3 5.5h14M3 14.5h14"/></svg>www.tidewrenmarine.com</span>
      <span><i class="social-dot"></i>/tidewrenmarinellc</span>
    </div>
  </section>

</div>
</body>
</html>
```